Kelo Wave Mint Business cards

Logo, tag line and photo on card
Agent Name
Title
Address
Phone number
Email
Website
Make logo on one side large by rotating  to portrait format.  Keep the background of the logo white.

Contact Information for Business Card
Slogan; Making Every Wave Count

```html
<!DOCTYPE html>
<html lang="en">
<head>
<meta charset="utf-8">
<title>Kelo Wave Mint – Business Card</title>
<link href="https://fonts.googleapis.com/css2?family=Open+Sans:wght@400;600;700&display=swap" rel="stylesheet">
<style>
  :root {
    --page-bg: #d9d2c8;
    --card-bg: #ebe4da;
    --card-edge: #f6f1ea;
    --logo-bg: #ffffff;
    --brand-red: #c2302f;
    --text-dark: #2e2b27;
    --text-body: #3d3935;
    --photo-light: #d8cbb8;
    --photo-dark: #3a3835;
  }
  * { margin: 0; padding: 0; box-sizing: border-box; }
  html, body {
    width: 1200px;
    height: 1047px;
    overflow: hidden;
    background: var(--page-bg);
    font-family: "Open Sans", Arial, sans-serif;
  }
  .business-card {
    position: absolute;
    left: 82px;
    top: 240px;
    width: 1036px;
    height: 566px;
    background: var(--card-bg);
    border: 2px solid var(--card-edge);
    border-radius: 26px;
    overflow: hidden;
    box-shadow: 0 10px 30px rgba(60, 45, 30, 0.18);
  }
  .brand-mark {
    position: absolute;
    left: 45px;
    top: 33px;
    width: 165px;
    height: 165px;
    background: var(--logo-bg);
    border: 3px solid var(--brand-red);
    border-radius: 6px;
    display: flex;
    align-items: center;
    justify-content: center;
    gap: 7px;
  }
  .brand-mark .brand-square {
    width: 10px;
    height: 10px;
    background: var(--brand-red);
    flex: none;
  }
  .brand-mark .brand-name {
    color: var(--text-dark);
    font-weight: 600;
    font-size: 16px;
    white-space: nowrap;
  }
  .slogan {
    position: absolute;
    left: 47px;
    top: 210px;
    color: var(--text-body);
    font-weight: 600;
    font-size: 17px;
  }
  .agent-name {
    position: absolute;
    left: 45px;
    top: 262px;
    color: var(--brand-red);
    font-weight: 700;
    font-size: 36px;
    letter-spacing: 0.5px;
  }
  .agent-title {
    position: absolute;
    left: 47px;
    top: 310px;
    color: var(--text-dark);
    font-weight: 600;
    font-size: 23px;
  }
  .contact-list {
    position: absolute;
    left: 45px;
    top: 356px;
    list-style: none;
  }
  .contact-list li {
    display: flex;
    align-items: center;
    gap: 10px;
    height: 34px;
    color: var(--text-body);
    font-size: 26px;
  }
  .contact-list svg { width: 24px; height: 24px; flex: none; }
  .address {
    position: absolute;
    left: 45px;
    top: 467px;
    color: var(--text-body);
    font-size: 26px;
    line-height: 33px;
  }
  .agent-photo {
    position: absolute;
    left: 612px;
    top: 33px;
    width: 424px;
    height: 533px;
    background: linear-gradient(180deg, var(--photo-light) 0%, #b9a996 45%, var(--photo-dark) 75%, #2c2b29 100%);
    border-bottom-right-radius: 24px;
  }
</style>
</head>
<body>
  <div class="business-card">
    <div class="brand-mark">
      <span class="brand-square"></span>
      <span class="brand-name">Kelo Wave Mint</span>
    </div>

    <p class="slogan">Making Every Wave Count</p>

    <h1 class="agent-name">MARCUS REED</h1>
    <p class="agent-title">Managing Director</p>

    <ul class="contact-list">
      <li>
        <svg viewBox="0 0 24 24" aria-hidden="true"><path fill="#c2302f" d="M6.6 10.8a15.1 15.1 0 0 0 6.6 6.6l2.2-2.2c.3-.3.7-.4 1-.2 1.1.4 2.3.6 3.6.6.6 0 1 .4 1 1V20c0 .6-.4 1-1 1A17 17 0 0 1 3 4c0-.6.4-1 1-1h3.5c.6 0 1 .4 1 1 0 1.3.2 2.5.6 3.6.1.3 0 .7-.2 1z"/></svg>
        <span>123 456 789</span>
      </li>
      <li>
        <svg viewBox="0 0 24 24" aria-hidden="true"><rect x="2" y="5" width="20" height="14" rx="2" fill="#c2302f"/><path d="M3 6.5l9 6.5 9-6.5" fill="none" stroke="#ffffff" stroke-width="1.8"/></svg>
        <span>info@yourmail.com</span>
      </li>
      <li>
        <svg viewBox="0 0 24 24" aria-hidden="true"><circle cx="12" cy="12" r="10" fill="#c2302f"/><path d="M2 12h20M12 2c3 3 3 17 0 20M12 2c-3 3-3 17 0 20" fill="none" stroke="#ffffff" stroke-width="1.4"/></svg>
        <span>www.yourwebsite.com</span>
      </li>
    </ul>

    <p class="address">Your address, City<br>State, Zip 1234</p>

    <div class="agent-photo" role="img" aria-label="Portrait photo of the agent, smiling, in a dark patterned shirt against a light background"></div>
  </div>
</body>
</html>
```